Animal Eye Clinic needs a Business card

We are a new veterinary ophthalmology practice (Ridgeline Pet Vision Care) and we need a business card designed. We only see animal eyes - we are not a regular veterinary clinic. We already have a logo. We are looking for a professional, good looking business card to hand out to our clients. We are looking for something simple but professional and contemporary. Our logo is likely the only picture/graphic that needs to be on the card.
Updates

Contact Information for Business Card

Delia Vossman, BSc, DVM, MSc, DipACVO
Veterinary Ophthalmologist

Phone: 250.418.3927
Email: ridgelinepetvisioncare@mailbox-example.net
Website: ridgelinepetvisioncare-example.net
Address: 1874 Thornbury Rd
Kelowna, BC, V1X 4M9

Colors

Designer to choose colors to be used in the design.

Requirements
Must have
• Our logo (attached)

```html
<!DOCTYPE html>
<html lang="en">
<head>
<meta charset="utf-8">
<title>Ridgeline Pet Vision Care — Business Card</title>
<link href="https://fonts.googleapis.com/css2?family=Open+Sans:wght@400;600&display=swap" rel="stylesheet">
<style>
  :root {
    --backdrop: #2a2a2c;
    --card: #333336;
    --card-deep: #2d2d30;
    --teal: #1a9cab;
    --ink: #f2f2f2;
    --emboss: #27272a;
    --emboss-light: #3d3d41;
  }
  * { margin: 0; padding: 0; box-sizing: border-box; }
  html, body { width: 1200px; height: 901px; overflow: hidden; }
  body {
    background: var(--backdrop);
    font-family: "Open Sans", Arial, sans-serif;
    display: flex;
    flex-direction: column;
    align-items: center;
    justify-content: center;
    gap: 40px;
  }
  .card {
    position: relative;
    width: 640px;
    height: 366px;
    background: var(--card);
    border-left: 4px solid var(--teal);
    border-bottom: 4px solid var(--teal);
    box-shadow: 0 10px 24px rgba(0,0,0,.45);
  }
  .wordmark {
    display: flex;
    align-items: center;
    gap: 14px;
    font-weight: 600;
    text-transform: uppercase;
    letter-spacing: 0.06em;
    line-height: 1.1;
  }
  .wordmark-dot { width: 54px; height: 54px; border-radius: 50%; flex: none; }
  .card-front .wordmark {
    position: absolute; left: 50%; top: 50%;
    transform: translate(-50%, -50%);
    font-size: 30px;
    color: var(--emboss);
    text-shadow: 0 1px 0 var(--emboss-light);
  }
  .card-front .wordmark-dot { background: var(--emboss); box-shadow: 0 1px 0 var(--emboss-light); }
  .card-back .wordmark {
    position: absolute; right: 36px; top: 50px;
    font-size: 22px; color: var(--teal);
    width: 330px;
  }
  .card-back .wordmark-dot { background: var(--teal); width: 46px; height: 46px; }
  .person { position: absolute; left: 40px; top: 150px; }
  .person-name { color: var(--teal); font-size: 19px; font-weight: 600; }
  .person-name .credentials { font-weight: 400; }
  .person-title { color: var(--ink); font-size: 16px; margin-top: 2px; }
  .divider {
    position: absolute; left: 40px; right: 40px; top: 212px;
    height: 1px; background: var(--ink);
  }
  .contact { position: absolute; left: 40px; top: 236px; list-style: none; }
  .contact li {
    display: flex; align-items: center; gap: 8px;
    color: var(--ink); font-size: 14.5px; line-height: 24px;
  }
  .contact svg { width: 13px; height: 13px; flex: none; }
  .contact .accent { color: var(--teal); }
  .address {
    position: absolute; right: 40px; bottom: 26px;
    color: var(--ink); font-size: 15.5px; line-height: 22px;
    font-style: normal;
  }
</style>
</head>
<body>
  <section class="card card-front" aria-label="Card front">
    <div class="wordmark">
      <span class="wordmark-dot"></span>
      <span>Ridgeline Pet<br>Vision Care</span>
    </div>
  </section>

  <section class="card card-back" aria-label="Card back">
    <div class="wordmark">
      <span class="wordmark-dot"></span>
      <span>Ridgeline Pet<br>Vision Care</span>
    </div>

    <div class="person">
      <p class="person-name">Delia Vossman<span class="credentials">, BSc, DVM, MSc, DipACVO</span></p>
      <p class="person-title">Veterinary Ophthalmologist</p>
    </div>

    <div class="divider"></div>

    <ul class="contact">
      <li>
        <svg viewBox="0 0 24 24" fill="var(--teal)"><path d="M6.6 10.8a15.2 15.2 0 0 0 6.6 6.6l2.2-2.2c.3-.3.7-.4 1-.2 1.1.4 2.3.6 3.6.6.6 0 1 .4 1 1V20c0 .6-.4 1-1 1A17 17 0 0 1 3 4c0-.6.4-1 1-1h3.5c.6 0 1 .4 1 1 0 1.3.2 2.5.6 3.6.1.3 0 .7-.2 1z"/></svg>
        250.418.3927
      </li>
      <li>
        <svg viewBox="0 0 24 24" fill="var(--teal)"><path d="M2 5h20v14H2z"/><path d="M2 5l10 8 10-8" fill="none" stroke="var(--card)" stroke-width="2"/></svg>
        ridgelinepetvisioncare@mailbox-example.net
      </li>
      <li>
        <svg viewBox="0 0 24 24" fill="none" stroke="var(--teal)" stroke-width="2"><circle cx="12" cy="12" r="10"/><ellipse cx="12" cy="12" rx="4" ry="10"/><path d="M2 12h20"/></svg>
        <span>www.<span class="accent">ridgelinepetvisioncare-example</span>.net</span>
      </li>
    </ul>

    <address class="address">
      1874 Thornbury Rd<br>
      Kelowna, BC, V1X 4M9
    </address>
  </section>
</body>
</html>
```